Web Design For Staffing Company

We need a homepage web design for a technical staffing company.

Please see attached brief for project details.

please make the site modern with bold colors while matching the logo

Be sure to read the attached breif in full beforehand.

Target Market(s)

technical companies looking to hire talent

Industry/Entity Type

Staffing

Number of Pages Required

1 page

Font styles to use
Sans Serif

```html
<!DOCTYPE html>
<html lang="en">
<head>
<meta charset="utf-8">
<title>Veltrix Staffing — Technical Staffing & Recruiting</title>
<link href="https://fonts.googleapis.com/css2?family=Mulish:wght@400;600;700;800&display=swap" rel="stylesheet">
<style>
:root{
  --blue:#3a8fd6;
  --navy:#1f5985;
  --link:#2a78c2;
  --ink:#222629;
  --body:#33383c;
  --muted:#5a6066;
  --band:#f0f5f9;
  --footer:#205b8b;
  --footer-bar:#2b72b3;
  --white:#fff;
}
*{margin:0;padding:0;box-sizing:border-box}
html,body{width:1200px;height:3595px;overflow:hidden}
body{position:relative;font-family:"Mulish",sans-serif;color:var(--body);background:var(--white)}
.abs{position:absolute}
.btn{position:absolute;display:flex;align-items:center;justify-content:center;color:var(--white);font-size:16px;font-weight:600;text-decoration:none;white-space:nowrap}
.btn.light{background:var(--blue)}
.btn.dark{background:var(--navy)}
.btn.black{background:#050505}
/* header */
.header{left:0;top:0;width:1200px;height:84px;background:var(--white)}
.brand{position:absolute;left:140px;top:22px;display:flex;align-items:center;gap:10px;font-weight:800;font-size:26px;color:var(--navy);white-space:nowrap}
.brand .dot{width:22px;height:22px;border-radius:50%;background:var(--navy)}
.nav a{position:absolute;top:32px;font-size:13px;color:var(--ink);text-decoration:none}
.nav a.active{color:var(--link)}
.search{left:925px;top:22px;width:133px;height:34px;border:1px solid #ccc;border-radius:3px;font-size:12px;color:#555;padding:9px 8px}
.search svg{position:absolute;right:8px;top:10px}
/* hero */
.hero{left:0;top:84px;width:1200px;height:577px;background:linear-gradient(100deg,#7a6a58 0%,#b9a993 22%,#d9dde1 45%,#a9b5c0 70%,#4c5763 100%)}
.hero h1{position:absolute;left:142px;top:192px;width:450px;font-size:27px;line-height:39px;font-weight:800;color:var(--white);text-shadow:0 2px 4px rgba(0,0,0,.45)}
/* intro */
.intro{left:150px;top:698px;width:900px;text-align:center;font-size:18.5px;line-height:33px;color:var(--ink)}
/* feature rows */
.photo{background:linear-gradient(135deg,#c9d4dd,#8e9fae 55%,#5e6e7c)}
.frame{border:5px solid var(--navy);border-radius:4px}
.copy{font-size:17px;line-height:30.5px;color:var(--ink)}
.copy strong{color:var(--link);font-weight:700}
/* testimonials */
.band{left:0;top:1832px;width:1200px;height:459px;background:var(--band)}
.sec-title{position:absolute;left:0;width:1200px;text-align:center;font-size:29px;font-weight:700;color:var(--ink)}
.avatar{left:565px;top:1956px;width:70px;height:70px;border-radius:50%;background:#d9dde1;border:2px solid #c8ced3}
.quote{left:170px;top:2050px;width:860px;text-align:center;font-size:16px;line-height:31px;color:var(--ink)}
.qmark{left:162px;top:2020px;font-size:80px;color:#c9d0d6;font-family:Georgia,serif;line-height:1}
.cite{left:0;top:2153px;width:1200px;text-align:center;font-size:12px;color:var(--ink)}
.cite b{color:var(--link);font-size:16px;font-weight:700}
.dots{left:570px;top:2197px;display:flex;gap:8px}
.dots span{width:14px;height:14px;border-radius:50%;border:1.5px solid #8a97a3}
.dots span.on{border-color:var(--link);background:radial-gradient(circle,var(--link) 3.5px,transparent 4px)}
/* blogs */
.card{position:absolute;top:2429px;width:293px;height:400px;background:var(--white);box-shadow:0 2px 10px rgba(0,0,0,.12)}
.card .thumb{height:188px}
.card .meta{position:absolute;left:18px;top:204px;font-size:12px;color:#444;display:flex;align-items:center;gap:6px}
.card h3{position:absolute;left:18px;top:228px;width:262px;font-size:17.5px;line-height:24px;font-weight:600;color:var(--ink)}
.card p{position:absolute;left:18px;width:262px;font-size:11px;line-height:20px;color:#555}
.card a{position:absolute;left:18px;top:354px;font-size:13px;color:var(--navy);text-decoration:underline}
/* cta */
.cta{position:absolute;top:2963px;height:232px;background:linear-gradient(135deg,#3d8bd0,#2f76bb)}
.cta h2{position:absolute;left:0;top:96px;width:100%;height:62px;text-align:center;font-size:23px;line-height:31px;font-weight:600;color:var(--white)}
.cta .btn{top:168px}
/* footer */
.footer{left:0;top:3258px;width:1200px;height:292px;background:var(--footer)}
.footer h4{position:absolute;top:78px;font-size:17px;font-weight:600;color:var(--white)}
.footer p{position:absolute;top:106px;font-size:12.5px;line-height:23px;color:#dfe9f2}
.footer .btn{font-size:13px;background:var(--blue);gap:7px;top:204px;height:30px;width:120px}
.footer .brand{left:830px;top:152px;color:var(--white);font-size:34px}
.footer .brand .dot{background:var(--white);width:26px;height:26px}
.bar{left:0;top:3550px;width:1200px;height:45px;background:var(--footer-bar)}
.bar small{position:absolute;left:142px;top:15px;font-size:12.5px;color:var(--white)}
.social{position:absolute;top:10px;width:25px;height:25px;border-radius:50%;border:1.5px solid var(--white)}
</style>
</head>
<body>

<header class="abs header">
  <div class="brand"><span class="dot"></span>Veltrix Staffing</div>
  <nav class="nav">
    <a class="active" style="left:509px">Home</a>
    <a style="left:580px">About</a>
    <a style="left:651px">Job Seekers</a>
    <a style="left:755px">Clients</a>
    <a style="left:830px">Contact Us</a>
  </nav>
  <div class="abs search">Search
    <svg width="12" height="12" viewBox="0 0 12 12"><circle cx="5" cy="5" r="3.8" fill="none" stroke="#222" stroke-width="1.6"/><path d="M8 8l3 3" stroke="#222" stroke-width="1.8"/></svg>
  </div>
</header>

<section class="abs hero" role="img" aria-label="Photo of a smiling professional woman in a meeting with a colleague in a bright office">
  <h1>The Right People For The Right Jobs! Bridging The Talent Gap In Technical Staffing</h1>
  <a class="btn light" style="left:141px;top:333px;width:134px;height:42px">Hire Talent</a>
  <a class="btn dark" style="left:286px;top:333px;width:134px;height:42px">Get Hired</a>
</section>

<p class="abs intro">Veltrix Staffing is a National Technical Staffing and Recruiting Solutions Provider founded in 2013 focused on matching contract and full time Engineering and IT professionals with new and exciting employment opportunities!</p>
<a class="btn dark" style="left:515px;top:819px;width:170px;height:38px;font-size:15px">Contact Us Today</a>

<div class="abs frame" style="left:163px;top:951px;width:353px;height:359px"></div>
<div class="abs photo" role="img" aria-label="Photo of a business team meeting around a glass table" style="left:141px;top:929px;width:354px;height:360px;border-radius:3px"></div>
<p class="abs copy" style="left:559px;top:998px;width:480px"><strong>We Love To Recruit!</strong> It's our passion and we take it very seriously! It is not easy for JOB SEEKERS to put their job search efforts and trust in the hands of someone else, especially when there are so many Staffing Firms to choose from. So how do you know you are choosing the best Staffing Representation possible?</p>
<a class="btn light" style="left:559px;top:1196px;width:127px;height:39px">Learn More</a>
<a class="btn dark" style="left:698px;top:1196px;width:125px;height:39px">View Jobs</a>

<p class="abs copy" style="left:144px;top:1440px;width:490px">Are you responsible for Technical Staffing within your organization? Are you satisfied with your current Supplier(s)' overall performance?<br>Does it appear they identify potential Candidate(s) based purely on “buzz-word” searches? Is it evident they just do not grasp the scope and responsibilities of your technical staffing need(s)?</p>
<a class="btn light" style="left:140px;top:1676px;width:126px;height:38px">Learn More</a>
<a class="btn dark" style="left:278px;top:1676px;width:127px;height:38px">Hire Talent</a>
<div class="abs frame" style="left:684px;top:1402px;width:354px;height:359px"></div>
<div class="abs photo" role="img" aria-label="Photo of a smiling woman talking with a colleague at a desk" style="left:705px;top:1381px;width:354px;height:360px;border-radius:3px"></div>

<section class="abs band"></section>
<h2 class="sec-title" style="top:1899px">Testimonials</h2>
<div class="abs avatar" role="img" aria-label="Reviewer avatar placeholder"></div>
<div class="abs qmark">“</div>
<p class="abs quote">Dan Mercer is an excellent recruiter. He is articulate, honest, has a good nature and is an effective information conduit between his clients and candidates. He gave me the feeling he is there for the big picture desiring to forge a future relationship that will be mutually beneficial to both of us.</p>
<p class="abs cite"><b>Sam R</b> - Electrical Test Engineer in the Automotive Sector</p>
<div class="abs dots"><span></span><span></span><span class="on"></span></div>

<h2 class="sec-title" style="top:2359px">Latest Blogs</h2>

<article class="card" style="left:141px">
  <div class="thumb" role="img" aria-label="Photo of a woman working on a laptop" style="background:linear-gradient(135deg,#e6e2dc,#9a8a7c 60%,#4a4440)"></div>
  <div class="meta">▦ June 17, 2019 &nbsp;|&nbsp; by veltrixstaffing</div>
  <h3>Ways To Make The Most Of The Hot Job Market</h3>
  <p style="top:285px">This is the tightest labor market I can remember. Unemployment is at a 50-year low and wage growth is at 3.2%,” said...[+]</p>
  <a>Read More</a>
</article>
<article class="card" style="left:453px">
  <div class="thumb" role="img" aria-label="Photo of a business handshake" style="background:linear-gradient(135deg,#dbe6f1,#7c9cc0 55%,#2c4f80)"></div>
  <div class="meta">▦ June 6, 2019 &nbsp;|&nbsp; by veltrixstaffing</div>
  <h3>Back To Basics: Meeting Employees' Needs To Improve Organizational Performance</h3>
  <p style="top:309px">The benefits of employee satisfaction are well-established, so HR professionals...[+]</p>
  <a>Read More</a>
</article>
<article class="card" style="left:766px">
  <div class="thumb" role="img" aria-label="Black and white portrait with a quote about technology" style="background:linear-gradient(135deg,#777,#2a2a2a 60%,#111)"></div>
  <div class="meta">▦ May 20, 2019 &nbsp;|&nbsp; by veltrixstaffing</div>
  <h3>5 Important Takeaways From Orbix's Two-Year Study Of Remote Work</h3>
  <p style="top:309px">Recently, the folks at Orbix published their findings from a two-year study...[+]</p>
  <a>Read More</a>
</article>

<a class="btn dark" style="left:537px;top:2867px;width:126px;height:37px">View All</a>

<section class="cta" role="img" aria-label="Blue-tinted photo of a team of professionals" style="left:141px;width:445px">
  <h2>Looking For Career-Minded<br>Candidates?</h2>
  <a class="btn black" style="left:152px;width:141px;height:37px">Request Talent</a>
</section>
<section class="cta" role="img" aria-label="Blue-tinted photo of a smiling job candidate" style="left:615px;width:444px">
  <h2>Looking For Career<br>Opportunities?</h2>
  <a class="btn black" style="left:151px;width:142px;height:37px">Search Jobs</a>
</section>

<footer class="abs footer">
  <h4 style="left:142px">Find Jobs</h4>
  <p style="left:142px;width:170px">Search Our extensive list of available jobs to find your match.</p>
  <h4 style="left:345px">Request An Employee</h4>
  <p style="left:346px;width:210px">We're here to provide the people you need to get work done.</p>
  <h4 style="left:585px">Get In Touch</h4>
  <p style="left:602px;width:180px">248 Harbor Lane, Suite 3, 2nd floor Brookfield, MA 01506</p>
  <svg class="abs" style="left:581px;top:111px" width="11" height="14" viewBox="0 0 11 14"><path d="M5.5 0A5 5 0 0 0 .5 5c0 4 5 9 5 9s5-5 5-9a5 5 0 0 0-5-5z" fill="#fff"/><circle cx="5.5" cy="5" r="2" fill="#205b8b"/></svg>
  <p style="left:602px;top:174px">555-214-8830</p>
  <svg class="abs" style="left:581px;top:179px" width="12" height="12" viewBox="0 0 12 12"><path d="M2 0l2.5 3-1.3 1.5a7 7 0 0 0 4.3 4.3L9 7.5l3 2.5-1.5 2C5 12 0 7 0 1.5z" fill="#fff"/></svg>
  <a class="btn" style="left:141px">
    <svg width="12" height="12" viewBox="0 0 12 12"><circle cx="5" cy="5" r="3.8" fill="none" stroke="#fff" stroke-width="1.6"/><path d="M8 8l3 3" stroke="#fff" stroke-width="1.8"/></svg>Search Now</a>
  <a class="btn" style="left:346px">
    <svg width="12" height="12" viewBox="0 0 12 12"><circle cx="6" cy="3.5" r="3" fill="#fff"/><path d="M0 12a6 5 0 0 1 12 0z" fill="#fff"/></svg>Start Today</a>
  <a class="btn" style="left:579px">
    <svg width="13" height="10" viewBox="0 0 13 10"><rect width="13" height="10" fill="#fff"/><path d="M0 0l6.5 5L13 0" fill="none" stroke="#3a8fd6" stroke-width="1.3"/></svg>Contact Us</a>
  <div class="brand"><span class="dot"></span>Veltrix Staffing</div>
</footer>
<div class="abs bar">
  <small>Copyright © 2020 Veltrix Staffing. All Rights Reserved.</small>
  <span class="social" style="left:964px" aria-label="Social link"></span>
  <span class="social" style="left:998px" aria-label="Social link"></span>
  <span class="social" style="left:1033px" aria-label="Social link"></span>
</div>

</body>
</html>
```